Business Card Design Project

i need a bussines car design
Velora Clinical Hypnotherapy

Daniel Wexford
Psychotherapy & Hypnosis

84261937 /0427591628

back of the card appoinment space.

file was provided on a PDF, LOgo , use the blu colorsa as well , elegant, clear,

Target Market(s)

young professional, caucasian , young mothers.

Industry/Entity Type

Business

```html
<!DOCTYPE html>
<html lang="en">
<head>
<meta charset="utf-8">
<title>Velora Clinical Hypnotherapy – Business Card</title>
<link href="https://fonts.googleapis.com/css2?family=Arimo:wght@400;700&display=swap" rel="stylesheet">
<style>
  :root {
    --page: #e9e6e1;
    --card-top: #ffffff;
    --card-bottom: #e4e7ea;
    --blue: #1f6fc0;
    --blue-dark: #14509a;
    --blue-light: #4f98dc;
    --ink: #2a2f36;
    --ink-soft: #5b6470;
    --photo-a: #d9cfc4;
    --photo-b: #b9a998;
    --badge: #8fbf3a;
  }
  * { box-sizing: border-box; margin: 0; padding: 0; }
  html, body { width: 1200px; height: 880px; overflow: hidden; }
  body {
    background: var(--page);
    font-family: "Arimo", Arial, sans-serif;
    color: var(--ink);
    position: relative;
  }
  .card {
    position: absolute;
    background: linear-gradient(180deg, var(--card-top) 0%, var(--card-bottom) 100%);
    box-shadow: 0 6px 18px rgba(0,0,0,.18);
    overflow: hidden;
  }

  /* Front */
  .card-front { left: 50px; top: 245px; width: 640px; height: 390px; }
  .partner-badge {
    position: absolute; left: 38px; top: 20px;
    width: 48px; height: 48px; border-radius: 50%;
    background: var(--badge); border: 3px solid #fff;
    box-shadow: 0 0 0 1px #c9cfd4;
  }
  .portrait {
    position: absolute; left: 10px; top: 80px; width: 225px; height: 310px;
    background: linear-gradient(180deg, var(--photo-a), var(--photo-b));
    border-radius: 110px 110px 0 0;
  }
  .brand {
    position: absolute; left: 255px; top: 62px;
    display: flex; align-items: center; gap: 10px;
  }
  .brand-mark {
    width: 26px; height: 26px; border-radius: 50%; background: var(--blue);
  }
  .brand-name { font-size: 27px; color: var(--ink); font-weight: 400; letter-spacing: .3px; }
  .brand-url {
    position: absolute; left: 291px; top: 98px;
    font-size: 11.5px; color: var(--ink-soft); letter-spacing: .6px;
    border-top: 1px solid var(--blue); padding-top: 3px; width: 320px;
  }
  .band {
    position: absolute; color: #fff;
    background: linear-gradient(180deg, var(--blue-light), var(--blue-dark));
    display: flex; align-items: center;
  }
  .band-name { left: 250px; top: 168px; width: 305px; height: 38px; font-size: 23px; font-weight: 700; padding-left: 42px; border-radius: 20px 22px 22px 0; }
  .band-role { left: 236px; top: 212px; width: 350px; height: 36px; font-size: 21px; padding-left: 40px; border-radius: 0 20px 20px 20px; }
  .band-phone { left: 228px; top: 268px; width: 380px; height: 42px; font-size: 24px; padding-left: 70px; border-radius: 10px 22px 22px 22px; }
  .phone-icon { position: absolute; right: -12px; top: -4px; width: 50px; height: 50px; }

  /* Back */
  .card-back { left: 760px; top: 120px; width: 390px; height: 640px; }
  .back-brand { position: absolute; left: 34px; top: 40px; display: flex; align-items: center; gap: 10px; }
  .back-brand .brand-name { font-size: 24px; }
  .back-url {
    position: absolute; left: 70px; top: 74px; font-size: 10px; color: var(--ink-soft);
    border-top: 1px solid var(--blue); padding-top: 2px; letter-spacing: .4px;
  }
  .contact { position: absolute; left: 34px; top: 118px; font-size: 15px; line-height: 22px; color: var(--ink); }
  .appointments-title {
    position: absolute; left: 34px; top: 218px;
    font-size: 31px; font-weight: 700; color: var(--blue);
  }
  .appointment-list { position: absolute; left: 34px; top: 278px; width: 322px; list-style: none; }
  .appointment-list li {
    display: flex; align-items: flex-end; gap: 4px;
    height: 54px; font-size: 15px; color: var(--ink);
  }
  .blank { border-bottom: 1px solid var(--ink); height: 16px; }
  .blank-time { width: 34px; }
  .blank-day { flex: 1; }
  .blank-date { width: 22px; }
  .footer-band {
    position: absolute; left: 0; bottom: 0; width: 100%; height: 76px;
    background: linear-gradient(180deg, var(--blue-light), var(--blue));
    color: #fff; padding: 12px 34px;
  }
  .footer-note { font-size: 10.5px; line-height: 14px; }
  .footer-reg { font-size: 14px; font-weight: 700; margin-top: 6px; }
</style>
</head>
<body>
  <section class="card card-front" aria-label="Business card front">
    <div class="partner-badge" aria-hidden="true"></div>
    <div class="portrait" role="img" aria-label="Portrait photo of the therapist, arms crossed, in a light shirt"></div>
    <div class="brand">
      <span class="brand-mark" aria-hidden="true"></span>
      <span class="brand-name">Velora Hypnotherapy</span>
    </div>
    <div class="brand-url">www.veloraclinicalhypnotherapy.com.au</div>
    <div class="band band-name">Daniel Wexford</div>
    <div class="band band-role">Psychotherapy &amp; Hypnosis</div>
    <div class="band band-phone">84261937 / 0427591628
      <svg class="phone-icon" viewBox="0 0 50 50" aria-hidden="true">
        <circle cx="25" cy="25" r="22" fill="#fff" stroke="#1f6fc0" stroke-width="3"/>
        <path d="M17 14c2-1 4 0 5 2l2 4c.5 1.3 0 2.6-1 3.3l-1.5 1c1.2 2.6 3.2 4.6 5.8 5.8l1-1.5c.8-1 2-1.5 3.3-1l4 2c2 1 3 3 2 5-1 2.5-3.5 3.8-6 3.2C21 35.8 14.2 29 12.2 20c-.6-2.5.7-5 3.2-6z" fill="#1f6fc0"/>
      </svg>
    </div>
  </section>

  <section class="card card-back" aria-label="Business card back">
    <div class="back-brand">
      <span class="brand-mark" aria-hidden="true"></span>
      <span class="brand-name">Velora Hypnotherapy</span>
    </div>
    <div class="back-url">www.veloraclinicalhypnotherapy.com.au</div>
    <p class="contact">
      By Appointment · Phone: 0427 591 628<br>
      48 Linden Street, Marlowe 3021<br>
      hello@veloraclinicalhypnotherapy.com.au
    </p>
    <h2 class="appointments-title">Your Appointments</h2>
    <ol class="appointment-list">
      <li>1. <span class="blank blank-time"></span>am/pm <span class="blank blank-day"></span><span class="blank blank-date"></span>/<span class="blank blank-date"></span>/<span class="blank blank-date"></span></li>
      <li>2. <span class="blank blank-time"></span>am/pm <span class="blank blank-day"></span><span class="blank blank-date"></span>/<span class="blank blank-date"></span>/<span class="blank blank-date"></span></li>
      <li>3. <span class="blank blank-time"></span>am/pm <span class="blank blank-day"></span><span class="blank blank-date"></span>/<span class="blank blank-date"></span>/<span class="blank blank-date"></span></li>
      <li>4. <span class="blank blank-time"></span>am/pm <span class="blank blank-day"></span><span class="blank blank-date"></span>/<span class="blank blank-date"></span>/<span class="blank blank-date"></span></li>
      <li>5. <span class="blank blank-time"></span>am/pm <span class="blank blank-day"></span><span class="blank blank-date"></span>/<span class="blank blank-date"></span>/<span class="blank blank-date"></span></li>
    </ol>
    <div class="footer-band">
      <p class="footer-note">To reschedule your appointment, please SMS or phone 0427 591 628 at least 24 hours prior to your allocated time. Thank you.</p>
      <p class="footer-reg">VPRA Registration No. NPM048215</p>
    </div>
  </section>
</body>
</html>
```